BUSINESS CARD DESIGN

NAME- DALE VORSKIN
PHONE NUMER - 555- 714-9082
EMAIL- OFFICE@TRV-GROUNDMAKRZ.COM
BACK OF CARD- SPEACIALIZES IN LAND CLEARING, FORESTRY MUCLHING AND EXCAVATION

Contact Information for Business Card

NAME- DALE VORSKIN PHONE NUMER - 555- 714-9082 EMAIL- OFFICE@TRV-GROUNDMAKRZ.COM BACK OF CARD- SPEACIALIZES IN LAND CLEARING , MUCLHING AND EXCAVATION

```html
<!DOCTYPE html>
<html lang="en">
<head>
<meta charset="utf-8">
<title>Business Card – Dale Vorskin</title>
<link rel="stylesheet" href="https://fonts.googleapis.com/css2?family=Montserrat:wght@300;400;700&display=swap">
<style>
  :root {
    --backdrop: #464646;
    --card: #151515;
    --ink: #ffffff;
    --edge: #2a2a2a;
  }
  html, body {
    margin: 0;
    padding: 0;
    width: 1200px;
    height: 801px;
    overflow: hidden;
    background: var(--backdrop);
    font-family: "Montserrat", Arial, sans-serif;
    color: var(--ink);
  }
  .stage {
    position: relative;
    width: 1200px;
    height: 801px;
  }
  .card {
    position: absolute;
    top: 252px;
    width: 520px;
    height: 297px;
    background: var(--card);
    border: 1px solid var(--edge);
    box-sizing: border-box;
    box-shadow: 0 10px 24px rgba(0,0,0,0.35);
  }
  .card--front { left: 50px; }
  .card--back  { left: 630px; }

  .identity {
    position: absolute;
    left: 62px;
    top: 128px;
    text-align: left;
  }
  .identity__name {
    margin: 0;
    font-weight: 700;
    font-size: 21px;
    letter-spacing: 0.5px;
    line-height: 1;
  }
  .identity__role {
    margin: 6px 0 0 22px;
    font-weight: 300;
    font-size: 13px;
    letter-spacing: 0.6px;
  }
  .divider {
    position: absolute;
    left: 262px;
    top: 118px;
    width: 1px;
    height: 54px;
    background: var(--ink);
  }
  .contacts {
    position: absolute;
    left: 282px;
    top: 112px;
    margin: 0;
    padding: 0;
    list-style: none;
  }
  .contacts__item {
    display: flex;
    align-items: center;
    gap: 8px;
    font-weight: 300;
    font-size: 12.5px;
    letter-spacing: 0.4px;
    line-height: 22px;
  }
  .contacts__icon {
    width: 11px;
    height: 11px;
    flex: none;
    fill: var(--ink);
  }
  .tagline {
    position: absolute;
    left: 38px;
    top: 160px;
    margin: 0;
    font-weight: 400;
    font-size: 12.5px;
    letter-spacing: 1px;
    white-space: nowrap;
  }
</style>
</head>
<body>
<main class="stage">
  <section class="card card--front" aria-label="Business card front">
    <div class="identity">
      <h1 class="identity__name">DALE VORSKIN</h1>
      <p class="identity__role">Managing Director</p>
    </div>
    <span class="divider"></span>
    <ul class="contacts">
      <li class="contacts__item">
        <svg class="contacts__icon" viewBox="0 0 12 12" aria-hidden="true"><path d="M1 3.5C1 2.5 3 1.5 6 1.5S11 2.5 11 3.5V4.5H8.5V3.5H3.5V4.5H1Z"/><rect x="2.5" y="5.5" width="7" height="5" rx="1"/></svg>
        555- 714-9082
      </li>
      <li class="contacts__item">
        <svg class="contacts__icon" viewBox="0 0 12 12" aria-hidden="true"><path d="M1 2.5H11V3.2L6 6.8 1 3.2Z"/><path d="M1 4.4L6 8 11 4.4V9.5H1Z"/></svg>
        office@trv-groundmakrz.com
      </li>
      <li class="contacts__item">
        <svg class="contacts__icon" viewBox="0 0 12 12" aria-hidden="true"><circle cx="6" cy="6" r="5"/><path d="M3 4.5C4 4 4.5 5 5.5 5S6 7 5 7.5 4 9 4 9" stroke="#151515" stroke-width="1" fill="none"/></svg>
        www.trv-groundmakrz.com
      </li>
    </ul>
  </section>

  <section class="card card--back" aria-label="Business card back">
    <p class="tagline">SPEACIALIZES IN LAND CLEARING , MUCLHING AND EXCAVATION</p>
  </section>
</main>
</body>
</html>
```